we need an experienced designer to design the tube for our toothpaste

Design guidelines:
1. On the front side, our product logo (‘K7320’) should be prominent enough.
2. Our brand logo (‘lumbrisk’) could be small-size and it's just a trademark indeed.

Some information here for your reference:
1. The color of toothpaste cap is white.
2. We hope that the primary color in the design is blue.
3.‘F’ in ‘K7320’ stands for ‘lumbrisk’ and ‘fluoride’.
4. We will use aluminum-plastic composite materials to make toothpaste tubes. In addition to the design, we also hope that you can make relevant suggestions on the special requirements of printing.

At last, we hope that you could submit both 2D design and 3D visual effects.

Attachments:
Product logo: K7320
Brand logo: lumbrisk
illustration ONE: metal braces
illustration TWO: clear aligners

Colors
0094D4
00A9DD
6FCCEA
C7EBF8
E9F6FB

Requirements
Must have
• as attached

```html
<!DOCTYPE html>
<html lang="en">
<head>
<meta charset="utf-8">
<title>K7320 Toothpaste Tube – Flat Artwork</title>
<link href="https://fonts.googleapis.com/css2?family=Fira+Sans+Condensed:ital,wght@0,400;0,500;0,800;1,400;1,800&family=Open+Sans:ital,wght@0,400;1,400&family=Fira+Sans:wght@900&display=swap" rel="stylesheet">
<style>
  :root{
    --tube-blue:#0072b8;
    --ink-blue:#1a64ad;
    --white:#ffffff;
    --silver-light:#e6e6e6;
    --silver-dark:#9a9a9a;
    --keyline:#2b2b2b;
    --seam:#8a8a8a;
    --dim-red:#e0301e;
    --dim-ink:#1a1a1a;
    --gum-light:#fbd9cd;
    --gum-dark:#e8707a;
  }
  html,body{margin:0;padding:0;width:1200px;height:1200px;overflow:hidden;background:#ffffff;}
  .artboard{display:block;width:1200px;height:1200px;}
  .title-main{font-family:"Fira Sans Condensed",sans-serif;font-weight:800;font-style:italic;fill:var(--ink-blue);}
  .title-sub{font-family:"Fira Sans Condensed",sans-serif;font-weight:400;fill:var(--ink-blue);}
  .back-heading{font-family:"Fira Sans Condensed",sans-serif;font-weight:500;fill:var(--ink-blue);}
  .product-mark{font-family:"Fira Sans",sans-serif;font-weight:900;fill:var(--white);}
  .brand-name{font-family:"Fira Sans",sans-serif;font-weight:900;fill:var(--white);}
  .claim{font-family:"Open Sans",sans-serif;font-style:italic;fill:var(--white);}
  .benefits{font-family:"Open Sans",sans-serif;fill:var(--white);}
  .copy{font-family:"Fira Sans Condensed",sans-serif;font-weight:400;fill:var(--white);}
  .dim-label{font-family:"Open Sans",sans-serif;fill:var(--dim-ink);}
  .dim-line{stroke:var(--dim-red);stroke-width:1;stroke-dasharray:5 4;fill:none;}
</style>
</head>
<body>
<svg class="artboard" viewBox="0 0 1200 1200" xmlns="http://www.w3.org/2000/svg">
  <defs>
    <linearGradient id="silver-band" x1="0" y1="0" x2="0" y2="1">
      <stop offset="0" stop-color="var(--silver-light)"/>
      <stop offset="1" stop-color="var(--silver-dark)"/>
    </linearGradient>
    <linearGradient id="mouth-tone" x1="0" y1="0" x2="0" y2="1">
      <stop offset="0" stop-color="var(--gum-light)"/>
      <stop offset="1" stop-color="var(--gum-dark)"/>
    </linearGradient>
  </defs>

  <g class="dimensions">
    <line class="dim-line" x1="280" y1="150" x2="330" y2="150"/>
    <line class="dim-line" x1="280" y1="236" x2="330" y2="236"/>
    <line class="dim-line" x1="280" y1="1019" x2="330" y2="1019"/>
    <line class="dim-line" x1="280" y1="1050" x2="330" y2="1050"/>
    <line class="dim-line" x1="312" y1="150" x2="312" y2="1050"/>
    <line class="dim-line" x1="330" y1="1050" x2="330" y2="1100"/>
    <line class="dim-line" x1="336" y1="1050" x2="336" y2="1100"/>
    <line class="dim-line" x1="908" y1="1050" x2="908" y2="1100"/>
    <line class="dim-line" x1="920" y1="1050" x2="920" y2="1100"/>
    <line class="dim-line" x1="330" y1="1068" x2="920" y2="1068"/>
    <text class="dim-label" font-size="13" transform="translate(306 212) rotate(-90)">14mm</text>
    <text class="dim-label" font-size="13" transform="translate(306 1046) rotate(-90)">5mm</text>
    <text class="dim-label" font-size="62" transform="translate(292 790) rotate(-90)">147.638mm</text>
    <text class="dim-label" font-size="46" x="625" y="1122" text-anchor="middle">97mm</text>
    <text class="dim-label" font-size="13" transform="translate(352 1110) rotate(-90)">1mm</text>
    <text class="dim-label" font-size="13" transform="translate(904 1110) rotate(-90)">2mm</text>
    <text class="dim-label" font-size="13" transform="translate(888 88) rotate(-90)">3*8mm</text>
  </g>

  <g class="tube-artwork" transform="translate(330 150)">
    <rect class="print-area" x="0" y="0" width="590" height="900" fill="var(--white)"/>
    <rect class="blue-body" x="0" y="279" width="590" height="621" fill="var(--tube-blue)"/>
    <rect class="silver-band" x="0" y="273" width="590" height="7" fill="url(#silver-band)"/>

    <path class="front-crest" d="M36 273 H319 V279 Q178 380 36 279 Z" fill="var(--white)"/>
    <path class="front-crest-edge" d="M36 279 Q178 380 319 279" fill="none" stroke="url(#silver-band)" stroke-width="7"/>

    <g class="front-panel">
      <text class="title-main" x="178" y="147" font-size="46" text-anchor="middle">Fluoride</text>
      <text class="title-main" x="178" y="197" font-size="46" text-anchor="middle">1450 ppm</text>
      <text class="title-sub" x="178" y="248" font-size="24" text-anchor="middle">Double Mint</text>

      <text class="product-mark" font-size="126" textLength="380" lengthAdjust="spacingAndGlyphs" transform="translate(228 843) rotate(-90)">K7320</text>

      <text class="brand-name" font-size="30" textLength="100" lengthAdjust="spacingAndGlyphs" transform="translate(120 843) rotate(-90)">lumbrisk</text>
      <circle class="brand-dot" cx="110" cy="730" r="5" fill="var(--white)"/>

      <text class="claim" font-size="14" textLength="186" lengthAdjust="spacingAndGlyphs" transform="translate(253 843) rotate(-90)">ORTHODONTIC TOOTHPASTE</text>
      <text class="claim" font-size="14" textLength="445" lengthAdjust="spacingAndGlyphs" transform="translate(279 843) rotate(-90)">ENHANCED CAVITY PREVENTION AND GUM PROTECTION FOR USE</text>
      <text class="claim" font-size="14" textLength="378" lengthAdjust="spacingAndGlyphs" transform="translate(299 843) rotate(-90)">WHEN WEARING METAL BRACES AND CLEAR ALIGNERS</text>
      <text class="copy" font-size="7" textLength="44" lengthAdjust="spacingAndGlyphs" transform="translate(298 366) rotate(-90)">NET WT. 85g</text>
    </g>

    <g class="back-panel">
      <text class="back-heading" font-size="23" text-anchor="middle" x="448" y="122" textLength="190" lengthAdjust="spacingAndGlyphs">PREMIUM ORAL CARE</text>
      <text class="back-heading" font-size="23" text-anchor="middle" x="448" y="146" textLength="216" lengthAdjust="spacingAndGlyphs">DURING ORTHODONTIC</text>
      <text class="back-heading" font-size="23" text-anchor="middle" x="448" y="170" textLength="110" lengthAdjust="spacingAndGlyphs">TREATMENT</text>
      <rect class="illustration" role="img" aria-label="Illustration of teeth with clear aligners" x="341" y="195" width="103" height="61" fill="url(#mouth-tone)"/>
      <rect class="illustration" role="img" aria-label="Illustration of teeth with metal braces" x="453" y="195" width="103" height="61" fill="url(#mouth-tone)"/>

      <text class="benefits" font-size="15" textLength="482" lengthAdjust="spacingAndGlyphs" transform="translate(366 843) rotate(-90)">● PREVENT CAVITY    ● FRESHEN BREATH    ● STRENGTHEN TEETH</text>

      <text class="copy" font-size="10" transform="translate(395 843) rotate(-90)">Directions</text>
      <text class="copy" font-size="10" textLength="514" lengthAdjust="spacingAndGlyphs" transform="translate(410 843) rotate(-90)">Apply at least one inch strip of the product onto a soft bristle toothbrush. Brush teeth thoroughly, for at least</text>
      <text class="copy" font-size="10" transform="translate(424 843) rotate(-90)">three minutes twice a day.</text>
      <text class="copy" font-size="10" transform="translate(452 843) rotate(-90)">Ingredients:</text>
      <text class="copy" font-size="10" textLength="514" lengthAdjust="spacingAndGlyphs" transform="translate(466 843) rotate(-90)">Aqua, Sorbitol, Hydrated Silica, Glycerin, PEG-12, Sodium Lauryl Sulfate, Aroma, Cellulose Gum, Titanium</text>
      <text class="copy" font-size="10" textLength="514" lengthAdjust="spacingAndGlyphs" transform="translate(480 843) rotate(-90)">Dioxide, Potassium Sorbate, Allantoin, Sodium Fluoride, Citric Acid, Peppermint Essence, Sodium Saccharin,</text>
      <text class="copy" font-size="10" transform="translate(493 843) rotate(-90)">CI 47005, CI 42090, Cinnamal.</text>
      <text class="copy" font-size="10" transform="translate(527 843) rotate(-90)">Warnings:</text>
      <text class="copy" font-size="10" textLength="305" lengthAdjust="spacingAndGlyphs" transform="translate(541 843) rotate(-90)">Do not ingest. Keep out of reach of children under 6 years of age.</text>
    </g>

    <line class="seam" x1="36" y1="7" x2="36" y2="900" stroke="var(--seam)" stroke-width="1"/>
    <line class="seam" x1="319" y1="7" x2="319" y2="900" stroke="var(--seam)" stroke-width="1"/>
    <path class="inner-keyline" d="M6 900 V7 H580 V900" fill="none" stroke="var(--keyline)" stroke-width="1.5"/>
    <rect class="outer-keyline" x="0" y="0" width="590" height="900" fill="none" stroke="var(--keyline)" stroke-width="2"/>
  </g>
</svg>
</body>
</html>
```